Professional & attention grabbing.

A business card design, front and back. I already have a logo I will attach, but I am open to something new as well.
Things to include:
Name:
Title:
Phone:
Email:
Wanting something that is professional but attention grabbing.
Also we do a lot of work using drones on natural gas pipelines (leading the future)if you want to include any of that. I'm open to ideas.
Target Market(s)
Natural gas transmission industry / greenhouse gas mitigation industry
Industry/Entity Type
Business
Colors
Designer to choose colors to be used in the design.
Look and feel
Each slider illustrates characteristics of the customer's brand and the style your logo design should communicate.

```html
<!DOCTYPE html>
<html lang="en">
<head>
<meta charset="utf-8">
<title>KV Field Inspections – Business Card</title>
<link href="https://fonts.googleapis.com/css2?family=Source+Sans+3:ital,wght@0,400;0,600;0,700;1,400&display=swap" rel="stylesheet">
<style>
  :root {
    --bg: #e4e4e4;
    --card-white: #ffffff;
    --charcoal: #363638;
    --red: #c01f25;
    --text-grey: #454547;
    --white: #ffffff;
  }
  * { margin: 0; padding: 0; box-sizing: border-box; }
  html, body {
    width: 1200px; height: 987px; overflow: hidden;
    background: var(--bg);
    font-family: "Source Sans 3", Arial, sans-serif;
  }
  .card {
    position: absolute; left: 293px; width: 615px; height: 352px;
    box-shadow: 0 2px 6px rgba(0,0,0,0.18);
    overflow: hidden;
  }
  .card--front { top: 130px; background: var(--card-white); }
  .card--back { top: 505px; background: var(--charcoal); }

  .brand {
    position: absolute; left: 33px; top: 42px;
    display: flex; align-items: center; gap: 14px;
  }
  .brand__square { width: 44px; height: 44px; background: var(--red); }
  .brand__name {
    color: var(--charcoal); font-weight: 700; font-size: 27px;
    line-height: 1.05; letter-spacing: 0.5px; text-transform: uppercase;
  }

  .contact {
    position: absolute; right: 25px; top: 176px; text-align: right;
  }
  .contact__name {
    color: var(--red); font-weight: 600; font-size: 23px; line-height: 1.15;
    letter-spacing: 0.3px;
  }
  .contact__title {
    color: var(--text-grey); font-size: 17px; line-height: 1.2; margin-bottom: 10px;
  }
  .contact__line {
    display: flex; justify-content: flex-end; align-items: center; gap: 8px;
    color: var(--text-grey); font-size: 16px; line-height: 24px;
  }
  .contact__line svg { width: 15px; height: 15px; fill: var(--red); }

  .stripe {
    position: absolute; left: 0; bottom: 0; width: 100%; height: 36px;
  }
  .web {
    position: absolute; color: var(--white); font-style: italic;
    letter-spacing: 2.4px; font-size: 16px;
  }
  .card--front .web { right: 26px; bottom: 8px; }

  .back-brand {
    position: absolute; left: 0; right: 0; top: 138px;
    display: flex; justify-content: center; align-items: center; gap: 18px;
  }
  .back-brand__square { width: 70px; height: 70px; background: var(--red); }
  .back-brand__name {
    color: var(--white); font-weight: 700; font-size: 38px; line-height: 1.05;
    text-transform: uppercase; letter-spacing: 1px;
  }
  .card--back .web {
    left: 0; right: 0; top: 302px; text-align: center;
    letter-spacing: 5px; font-size: 17px;
  }
</style>
</head>
<body>
  <section class="card card--front">
    <div class="brand">
      <div class="brand__square"></div>
      <div class="brand__name">KV Field<br>Inspections</div>
    </div>

    <div class="contact">
      <div class="contact__name">DANIEL REYES</div>
      <div class="contact__title">CEO/FOUNDER</div>
      <div class="contact__line">555 214 0837
        <svg viewBox="0 0 24 24"><path d="M6.6 10.8a15.1 15.1 0 0 0 6.6 6.6l2.2-2.2a1 1 0 0 1 1-.25 11.4 11.4 0 0 0 3.6.57 1 1 0 0 1 1 1V20a1 1 0 0 1-1 1A17 17 0 0 1 3 4a1 1 0 0 1 1-1h3.5a1 1 0 0 1 1 1c0 1.25.2 2.45.57 3.57a1 1 0 0 1-.25 1z"/></svg>
      </div>
      <div class="contact__line">info@kvfield.com
        <svg viewBox="0 0 24 24"><path d="M2 5h20v14H2z M2 5l10 8 10-8" fill="var(--red)"/><path d="M3 6l9 7 9-7" fill="none" stroke="#fff" stroke-width="1.6"/></svg>
      </div>
    </div>

    <svg class="stripe" viewBox="0 0 615 36" preserveAspectRatio="none">
      <path d="M0 12 H358 Q366 12 368 4 Q370 0 378 0 H615 V36 H0 Z" fill="var(--charcoal)" opacity="0"/>
      <rect x="0" y="14" width="362" height="5" fill="var(--red)"/>
      <rect x="0" y="21" width="362" height="3" fill="#9a9a9c"/>
      <path d="M366 36 L372 8 Q374 0 384 0 H615 V36 Z" fill="var(--charcoal)"/>
    </svg>
    <div class="web">www.kvfield.com</div>
  </section>

  <section class="card card--back">
    <div class="back-brand">
      <div class="back-brand__square"></div>
      <div class="back-brand__name">KV Field<br>Inspections</div>
    </div>
    <div class="web">www.kvfield.com</div>
  </section>
</body>
</html>
```